Business Card for Industrial Distributor

We need a business card design for an industrial distributor. We sell machine parts for the manufacturing and oil industry. We would like the cards to look clean and modern but with a touch of industry.

Our colors are blue/white.

Please feel free to visit our website www.korvelpartsco.com

Target Market(s)

mexican manufacturers in the automobile/aerospace industry

Industry/Entity Type

Industrial

Colors
ffffff
0555a3

```html
<!DOCTYPE html>
<html lang="en">
<head>
<meta charset="utf-8">
<title>Korvel Business Card</title>
<link rel="stylesheet" href="https://fonts.googleapis.com/css2?family=Exo+2:wght@800&family=Montserrat:wght@400;600&display=swap">
<style>
  :root {
    --brand-blue: #283a96;
    --accent-blue: #0555a3;
    --light-blue: #1a7cc4;
    --white: #ffffff;
    --faint: #e9eef7;
    --stage: #e4e6ea;
  }
  * { margin: 0; padding: 0; box-sizing: border-box; }
  html, body { width: 1200px; height: 900px; overflow: hidden; }
  body { background: var(--stage); position: relative; font-family: "Montserrat", sans-serif; }

  .card {
    position: absolute;
    width: 560px;
    height: 320px;
    border-radius: 22px;
    overflow: hidden;
    box-shadow: 0 10px 30px rgba(0,0,0,0.18);
  }

  /* Back side */
  .card-back { left: 80px; top: 70px; background: var(--brand-blue); }
  .back-mark {
    position: absolute; left: 50%; top: 48px; transform: translateX(-50%);
    display: flex; flex-direction: column; align-items: center; gap: 14px;
  }
  .back-mark .dot { width: 150px; height: 150px; border-radius: 50%; background: var(--white); }
  .back-mark .name {
    font-family: "Exo 2", sans-serif; font-weight: 800; font-size: 30px;
    color: var(--white); letter-spacing: 1px;
  }
  .back-url {
    position: absolute; left: 0; right: 0; bottom: 34px; text-align: center;
    color: var(--white); font-size: 15px; letter-spacing: 0.5px;
  }
  .back-url b { font-weight: 600; }

  /* Front side */
  .card-front { left: 560px; top: 500px; background: var(--white); }
  .front-band {
    position: absolute; left: 0; top: 0; bottom: 0; width: 120px;
    background: var(--brand-blue);
  }
  .front-rule {
    position: absolute; left: 126px; top: 0; bottom: 0; width: 3px;
    background: var(--light-blue);
  }
  .front-deco {
    position: absolute; right: -30px; top: -40px; width: 290px; height: 290px;
    border-radius: 50%; background: var(--faint);
  }
  .front-dot {
    position: absolute; left: 64px; top: 104px; width: 84px; height: 84px;
    border-radius: 50%; background: var(--accent-blue);
    border: 3px solid var(--white);
  }
  .brand-name {
    position: absolute; left: 166px; top: 86px;
    font-family: "Exo 2", sans-serif; font-weight: 800; font-size: 72px;
    color: var(--brand-blue); line-height: 1; letter-spacing: 1px;
  }
  .person { position: absolute; left: 172px; top: 180px; }
  .person .full-name { font-weight: 600; font-size: 19px; color: var(--brand-blue); letter-spacing: 0.5px; }
  .person .role { font-size: 12px; color: var(--light-blue); margin-top: 2px; }
  .address { position: absolute; left: 192px; top: 222px; font-size: 13px; color: var(--light-blue); line-height: 1.3; }
  .contacts { position: absolute; left: 186px; top: 262px; list-style: none; font-size: 12.5px; color: var(--light-blue); }
  .contacts li { display: flex; align-items: center; gap: 8px; line-height: 1.35; }
  .contacts svg { width: 10px; height: 10px; fill: var(--brand-blue); }
  .contacts .web { color: var(--brand-blue); font-weight: 600; }
</style>
</head>
<body>

<section class="card card-back" aria-label="Card back">
  <div class="back-mark">
    <div class="dot"></div>
    <div class="name">Korvel</div>
  </div>
  <p class="back-url">www.<b>korvelpartsco</b>.com</p>
</section>

<section class="card card-front" aria-label="Card front">
  <div class="front-deco"></div>
  <div class="front-band"></div>
  <div class="front-rule"></div>
  <div class="front-dot"></div>
  <h1 class="brand-name">Korvel</h1>
  <div class="person">
    <p class="full-name">Marco Ellison</p>
    <p class="role">Director</p>
  </div>
  <p class="address">P.O. Box 4412<br>Fairhaven, MI 49087</p>
  <ul class="contacts">
    <li><svg viewBox="0 0 10 10"><path d="M2 0h2l1 3-1.3 1a6 6 0 0 0 2.3 2.3L7 5l3 1v2a2 2 0 0 1-2 2A8 8 0 0 1 0 2a2 2 0 0 1 2-2z"/></svg>+330 5182-0394</li>
    <li><svg viewBox="0 0 10 10"><path d="M0 2h10v6H0z M0.8 2.4 5 5.6l4.2-3.2" stroke="#fff" stroke-width="0.8"/></svg>info@korvelpartsco.com</li>
    <li><svg viewBox="0 0 10 10"><circle cx="5" cy="5" r="5"/></svg><span class="web">www.korvelpartsco.com</span></li>
  </ul>
</section>

</body>
</html>
```